Four in One (Flexible infographic for Content Management Industry)

See attachment.
A graphic depicting 4 products, where each can stand on its own and each can be combined with others, but where, if all are taken together, the best result is achieved (the "super product").
Intended use is web. See attached file as an example.
The most basic idea is as the attached diagram shows, where 4 rectangles are arranged in a quadrangle, with a middle rectangle in the center representing the combined 4 products. This concept is fine except it is a bit too obvious as it stands. We are looking for either a variation of this or another concept.
The audience is technical + professional + enterprise - NOT consumers. Hence the design should be conservative in nature.
We are aware of tools like as Canva or Pictogram where such graphics are available, but we are looking for something with a bit more imagination and flexibility.
This graphic should be targeted to web sites and be delivered with vector-based (SVG) graphics.

```html
<!DOCTYPE html>
<html lang="en">
<head>
<meta charset="utf-8">
<title>Four in One – Super Product</title>
<link href="https://fonts.googleapis.com/css2?family=Fira+Sans+Condensed:ital,wght@0,400;0,500;0,700;1,400&family=Fira+Sans+Extra+Condensed:wght@900&display=swap" rel="stylesheet">
<style>
  :root{
    --bg:#ffffff;
    --card:#e8f4fc;
    --ink:#2b2b2b;
    --muted:#3a3a3a;
    --rule:#9a9a9a;
    --purple:#6e4fbd;
    --purple-title:#6a45c6;
    --red:#ff4520;
    --red-title:#f03c1c;
    --blue:#4a62fb;
    --blue-title:#4a5ff2;
    --orange:#ffa40a;
    --button:#b79cc9;
    --hub:#f1f1f1;
  }
  *{box-sizing:border-box;margin:0;padding:0}
  html,body{width:1200px;height:768px;overflow:hidden;background:var(--bg)}
  body{font-family:"Fira Sans Condensed",sans-serif;color:var(--ink)}
  .canvas{position:relative;width:1200px;height:768px}
  .shapes{position:absolute;inset:0}
  .card-shadow{filter:drop-shadow(3px 4px 4px rgba(0,0,0,.45))}
  .hub-title{position:absolute;left:451px;top:334px;width:292px;text-align:center;
    font-family:"Fira Sans Extra Condensed",sans-serif;font-weight:900;font-size:45px;line-height:39px;color:#1f1f1f;letter-spacing:-.5px}
  .module{position:absolute;width:330px}
  .module.left{left:147px}
  .module.right{right:158px;text-align:right}
  .module-title{font-weight:500;font-size:23px;line-height:26px;white-space:nowrap}
  .module-text{font-size:12.3px;line-height:16.5px;color:var(--muted);margin-top:4px}
  .right .module-text{text-align:left;margin-left:auto}
  .module-rule{height:2px;background:linear-gradient(90deg,var(--rule),rgba(154,154,154,.15));margin:10px 0 9px}
  .right .module-rule{background:linear-gradient(270deg,var(--rule),rgba(154,154,154,.15))}
  .features{list-style:none;font-style:italic;font-size:12px;line-height:16.8px;color:#222}
  .left .features li::before{content:"✓ ";font-style:normal}
  .right .features li::after{content:" ✓";font-style:normal}
  .learn-more{display:inline-flex;align-items:center;gap:3px;margin-top:9px;height:18px;padding:0 7px;
    background:var(--button);border-radius:3px;color:#fff;font-weight:700;font-size:8.5px;letter-spacing:.3px;
    box-shadow:1px 2px 2px rgba(0,0,0,.45)}
  .purple .module-title{color:var(--purple-title)}
  .blue .module-title{color:var(--blue-title)}
  .red .module-title,.orange .module-title{color:var(--red-title)}
</style>
</head>
<body>
<div class="canvas">
  <svg class="shapes" width="1200" height="768" viewBox="0 0 1200 768" aria-hidden="true">
    <defs>
      <path id="card-shape" d="M133,101 L467,101 Q491,101 491,125 L491,222 C491,240 468,246 452,268 C434,296 434,326 402,326 L133,326 Q109,326 109,302 L109,125 Q109,101 133,101 Z"/>
      <filter id="hub-shadow" x="-20%" y="-20%" width="140%" height="140%">
        <feDropShadow dx="0" dy="3" stdDeviation="5" flood-opacity=".35"/>
      </filter>
    </defs>
    <rect x="154" y="124" width="431" height="238" rx="52" fill="var(--purple)"/>
    <rect x="609" y="124" width="433" height="240" rx="52" fill="var(--red)"/>
    <rect x="154" y="390" width="431" height="240" rx="52" fill="var(--blue)"/>
    <rect x="609" y="392" width="433" height="238" rx="52" fill="var(--orange)"/>
    <g class="card-shadow" fill="var(--card)">
      <use href="#card-shape"/>
      <use href="#card-shape" transform="translate(1191 0) scale(-1 1)"/>
      <use href="#card-shape" transform="translate(0 755) scale(1 -1)"/>
      <use href="#card-shape" transform="translate(1191 755) scale(-1 -1)"/>
    </g>
    <circle cx="597" cy="377" r="146" fill="var(--hub)" stroke="#ffffff" stroke-width="6" filter="url(#hub-shadow)"/>
    <path d="M109,128 H125 A11,11 0 0 1 125,150 H109 Z" fill="var(--purple)"/>
    <g fill="none" stroke="#fff" stroke-width="1.2">
      <path d="M120,133 H126 L129,136 V145 H120 Z"/>
      <path d="M122,139 H127 M122,141.5 H127 M122,143.5 H125"/>
    </g>
    <path d="M1082,128 H1066 A11,11 0 0 0 1066,150 H1082 Z" fill="var(--red)"/>
    <path d="M1059,144 H1072 A3.5,3.5 0 0 0 1071,137 A5,5 0 0 0 1062,136 A4,4 0 0 0 1059,144 Z M1065.5,146 V139 M1063,141 L1065.5,138.5 L1068,141" fill="none" stroke="#fff" stroke-width="1.3" stroke-linejoin="round"/>
    <path d="M109,453 H125 A11,11 0 0 1 125,475 H109 Z" fill="var(--blue)"/>
    <g fill="none" stroke="#fff" stroke-width="1.2">
      <rect x="119" y="458" width="11" height="11"/>
      <path d="M122,466 V463 M124.5,466 V461 M127,466 V462.5"/>
    </g>
    <path d="M1082,453 H1066 A11,11 0 0 0 1066,475 H1082 Z" fill="var(--orange)"/>
    <g fill="none" stroke="#fff" stroke-width="1.2" stroke-linecap="round">
      <path d="M1060,464 A6,6 0 0 1 1072,464"/>
      <path d="M1063,464 A3,3 0 0 1 1069,464 V468"/>
      <path d="M1066,464 V470 M1058,461 H1061 M1071,461 H1074 M1059,467 H1062 M1071,467 H1074"/>
    </g>
  </svg>

  <div class="hub-title">SUPER<br>PRODUCT</div>

  <section class="module left purple" style="top:124px">
    <h2 class="module-title">Document Management</h2>
    <p class="module-text">Streamline document organization, access, and collaboration with easier file storage and sharing, leading to more efficient workflows.</p>
    <div class="module-rule" style="width:300px"></div>
    <ul class="features">
      <li>Centralized Document Control</li>
      <li>Collaborative Workspace Integration</li>
      <li>Automated Compliance Tracking</li>
      <li>Check 4</li>
    </ul>
    <span class="learn-more">LEARN MORE ⊙</span>
  </section>

  <section class="module right red" style="top:124px;width:320px">
    <h2 class="module-title">Security and Compliance</h2>
    <p class="module-text" style="width:314px">Benefit from tailored cloud solutions, secure data storage, and expert disaster recovery planning for reliable and scalable IT operations.</p>
    <div class="module-rule" style="width:300px;margin-left:auto"></div>
    <ul class="features">
      <li>Custom Cloud Solutions</li>
      <li>Secure Data Storage</li>
      <li>Expert Disaster Recovery</li>
      <li>Check 4</li>
    </ul>
    <span class="learn-more">LEARN MORE ⊙</span>
  </section>

  <section class="module left blue" style="top:451px">
    <h2 class="module-title">Enterprise Resource Planning</h2>
    <p class="module-text" style="width:260px">Simplify management across finance, sales, and operations, enabling better decision-making and improved productivity.</p>
    <div class="module-rule" style="width:300px;margin-top:12px"></div>
    <ul class="features">
      <li>Integrated Business Processes</li>
      <li>Enhanced Decision-Making</li>
      <li>Productivity Improvement</li>
      <li>Check 4</li>
    </ul>
    <span class="learn-more">LEARN MORE ⊙</span>
  </section>

  <section class="module right orange" style="top:451px;width:300px">
    <h2 class="module-title">Security and Compliance</h2>
    <p class="module-text" style="width:276px">Turn scanned documents into easily searchable digital archives, boosting efficiency and accessibility.</p>
    <div class="module-rule" style="width:300px;margin-left:auto;margin-top:29px"></div>
    <ul class="features">
      <li>Instant searchable Archives with OCR</li>
      <li>Automated Document Classification</li>
      <li>Quillbay and Cloud Blob Ready</li>
      <li>Check 4</li>
    </ul>
    <span class="learn-more">LEARN MORE ⊙</span>
  </section>
</div>
</body>
</html>
```